TA BRAMLEY BUSINESS CARD DESIGN PROJECT

We need to utilize our logo that was expertly created on PixelHarbor and now need to match this with a business card design.

```html
<!DOCTYPE html>
<html lang="en">
<head>
<meta charset="utf-8">
<title>TA BRAMLEY Business Card</title>
<link rel="stylesheet" href="https://fonts.googleapis.com/css2?family=Montserrat:wght@400;700&display=swap">
<style>
  :root {
    --brand-blue: #1157ad;
    --card-black: #161616;
    --card-white: #ffffff;
    --backdrop: #e6e6e6;
    --text-light: #ffffff;
  }
  * { box-sizing: border-box; margin: 0; padding: 0; }
  html, body {
    width: 1200px; height: 900px; overflow: hidden;
    background: var(--backdrop);
    font-family: "Montserrat", sans-serif;
  }
  .canvas {
    position: relative; width: 1200px; height: 900px;
    display: flex; flex-direction: column; align-items: center;
    justify-content: center; gap: 40px;
  }
  .card {
    position: relative; width: 700px; height: 400px;
    border-radius: 24px; overflow: hidden;
    box-shadow: 0 6px 20px rgba(0,0,0,0.18);
  }
  .card-front {
    background: var(--brand-blue);
    display: flex; align-items: center; justify-content: center;
  }
  .wordmark {
    font-weight: 700; letter-spacing: 0.12em; text-transform: uppercase;
  }
  .card-front .wordmark { color: var(--text-light); font-size: 64px; }
  .card-back { background: var(--card-white); }
  .card-back .backdrop-shape { position: absolute; inset: 0; }
  .card-back .wordmark {
    position: absolute; left: 60px; top: 100px;
    color: var(--brand-blue); font-size: 40px;
  }
  .contact-block {
    position: absolute; right: 40px; top: 80px;
    text-align: right; color: var(--text-light);
  }
  .accent-bar {
    position: absolute; right: 0; top: 74px;
    width: 12px; height: 52px; background: var(--brand-blue);
  }
  .person-name {
    color: var(--brand-blue); font-weight: 700; font-size: 26px;
    letter-spacing: 0.02em;
  }
  .person-role { font-size: 17px; margin-top: 2px; }
  .contact-list { list-style: none; margin-top: 26px; font-size: 17px; line-height: 1.7; }
  .contact-list li { display: flex; align-items: center; justify-content: flex-end; gap: 12px; }
  .contact-list svg { width: 14px; height: 14px; fill: var(--brand-blue); }
  .address {
    position: absolute; left: 36px; bottom: 20px;
    color: var(--text-light); font-size: 16px; line-height: 1.35;
  }
</style>
</head>
<body>
<main class="canvas">
  <section class="card card-front">
    <span class="wordmark">TA BRAMLEY</span>
  </section>

  <section class="card card-back">
    <svg class="backdrop-shape" viewBox="0 0 700 400" preserveAspectRatio="none" aria-hidden="true">
      <path fill="var(--card-black)" d="M560,0 C480,40 440,165 395,245 C345,315 200,330 0,290 L0,400 L700,400 L700,0 Z"/>
      <path fill="var(--brand-blue)" d="M535,0 C460,40 415,160 370,240 C320,310 180,320 0,275 L0,286 C190,330 335,320 385,245 C430,165 470,40 553,0 Z"/>
    </svg>
    <span class="wordmark">TA BRAMLEY</span>
    <div class="accent-bar"></div>
    <div class="contact-block">
      <p class="person-name">DANIEL HART</p>
      <p class="person-role">Managing Director</p>
      <ul class="contact-list">
        <li>123 456 789
          <svg viewBox="0 0 16 16"><path d="M3 1h3l1 4-2 1c1 2 3 4 5 5l1-2 4 1v3c0 1-1 2-2 2C7 15 1 9 1 3c0-1 1-2 2-2z"/></svg></li>
        <li>info@yourmail.com
          <svg viewBox="0 0 16 16"><path d="M1 3h14v10H1z M1 3l7 6 7-6" /></svg></li>
        <li>www.yourwebsite.com
          <svg viewBox="0 0 16 16"><circle cx="8" cy="8" r="7"/></svg></li>
      </ul>
    </div>
    <p class="address">Your address, City<br>State, Zip 1234</p>
  </section>
</main>
</body>
</html>
```